Brindovalle Business cards

Dear team, I need to get the design file to suit it to our team. The focus of the business card is the Automotive Market and the design must be in black colour and the logo must be in glossy black. On the front of the card I need to get the following info:

- Name and Surname
- Title
- eMail
- Phone Number
- Skype account
- domain address

```html
<!DOCTYPE html>
<html lang="es">
<head>
<meta charset="utf-8">
<title>Brindovalle – Tarjetas de visita</title>
<link href="https://fonts.googleapis.com/css2?family=Montserrat:wght@400;500;700;800&display=swap" rel="stylesheet">
<style>
  :root {
    --stage: #e6e6e8;
    --card: #2b2b2d;
    --card-back: #1e1e20;
    --gloss-black: #0d0d0e;
    --gloss-grey: #4a4a4e;
    --accent: #e0232a;
    --text: #f2f2f2;
    --muted: #c9c9cc;
  }
  * { box-sizing: border-box; margin: 0; padding: 0; }
  html, body { width: 1200px; height: 1186px; overflow: hidden; }
  body {
    background: var(--stage);
    font-family: "Montserrat", Arial, sans-serif;
    position: relative;
  }
  .card {
    position: absolute;
    left: 150px;
    width: 900px;
    height: 514px;
    border-radius: 30px;
    overflow: hidden;
  }
  .card--back { top: 56px; background: var(--card-back); }
  .card--front { top: 616px; background: var(--card); }

  /* back */
  .pattern-area {
    position: absolute; inset: 0;
    background: linear-gradient(135deg, #5a5a5e 0%, #2a2a2c 40%, #141415 100%);
  }
  .back-brand {
    position: absolute;
    left: 300px; top: 215px;
    display: flex; align-items: center; gap: 18px;
  }
  .brand-square {
    width: 66px; height: 66px;
    background: var(--accent);
  }
  .back-brand .brand-name {
    font-weight: 800; font-size: 64px; color: #ffffff; letter-spacing: -1px;
  }

  /* front */
  .front-brand {
    position: absolute;
    left: 90px; top: 150px;
    display: flex; align-items: center; gap: 20px;
  }
  .front-brand .brand-square {
    width: 96px; height: 96px;
    background: var(--gloss-black);
  }
  .front-brand .brand-name {
    font-weight: 800; font-size: 96px; color: var(--gloss-black); letter-spacing: -2px;
  }
  .person {
    position: absolute;
    left: 90px; top: 330px;
    width: 380px;
    text-align: right;
  }
  .person__name {
    color: var(--accent); font-weight: 700; font-size: 30px; letter-spacing: 1px;
    text-transform: uppercase;
  }
  .person__role { color: var(--text); font-size: 20px; margin-bottom: 18px; }
  .person__address { color: var(--text); font-size: 19px; line-height: 1.3; }
  .divider {
    position: absolute; left: 500px; top: 300px;
    width: 2px; height: 140px; background: var(--accent);
  }
  .contacts {
    position: absolute; left: 530px; top: 290px;
    list-style: none;
  }
  .contacts li {
    display: flex; align-items: center; gap: 12px;
    color: var(--text); font-size: 19px; line-height: 38px;
  }
  .contacts svg { width: 18px; height: 18px; flex: none; fill: var(--accent); }
</style>
</head>
<body>

<section class="card card--back" aria-label="Reverso de la tarjeta">
  <div class="pattern-area" role="img" aria-label="Patrón decorativo repetido del símbolo de la marca en negro brillante"></div>
  <div class="back-brand">
    <span class="brand-square"></span>
    <span class="brand-name">Brindovalle</span>
  </div>
</section>

<section class="card card--front" aria-label="Anverso de la tarjeta">
  <div class="front-brand">
    <span class="brand-square"></span>
    <span class="brand-name">Brindovalle</span>
  </div>

  <div class="person">
    <p class="person__name">Marco Ledesma</p>
    <p class="person__role">Comercial</p>
    <p class="person__address">Pol. Ind. Las Arenas C/4 nº 22<br>41710 Villa Serrana</p>
  </div>

  <span class="divider"></span>

  <ul class="contacts">
    <li>
      <svg viewBox="0 0 24 24" aria-hidden="true"><path d="M6.6 10.8a15 15 0 0 0 6.6 6.6l2.2-2.2c.3-.3.7-.4 1-.2 1.1.4 2.3.6 3.6.6.6 0 1 .4 1 1V20c0 .6-.4 1-1 1A17 17 0 0 1 3 4c0-.6.4-1 1-1h3.5c.6 0 1 .4 1 1 0 1.3.2 2.5.6 3.6.1.3 0 .7-.2 1z"/></svg>
      612 40 58 27
    </li>
    <li>
      <svg viewBox="0 0 24 24" aria-hidden="true"><path d="M2 5h20v14H2z M2 5l10 8 10-8" /></svg>
      redazione@brindovalle.com
    </li>
    <li>
      <svg viewBox="0 0 24 24" aria-hidden="true"><circle cx="12" cy="12" r="10"/></svg>
      @brindovalle
    </li>
    <li>
      <svg viewBox="0 0 24 24" aria-hidden="true"><path d="M12 2a10 10 0 1 0 0 20 10 10 0 0 0 0-20zm0 2c1.3 1.6 2.2 4.3 2.3 7H9.7C9.8 8.3 10.7 5.6 12 4zM9.7 13h4.6c-.1 2.7-1 5.4-2.3 7-1.3-1.6-2.2-4.3-2.3-7z"/></svg>
      www.brindovalle.com
    </li>
  </ul>
</section>

</body>
</html>
```